New Business Card Design Project

Need a design that will create an impact / strong impression towards our clients for our business. We are in the lighting business and we do lighting retrofits for large commercial to industrial clientele.

Target Market(s)

Lighting Industry

Industry/Entity Type

Business

Font styles to use
Other font styles liked:
• we would like to use the font on our logo, not sure what it is though..

Requirements
Must have
• Our logo.
Nice to have
• We are open to suggestions that have to do with lighting.

```html
<!DOCTYPE html>
<html lang="en">
<head>
<meta charset="utf-8">
<title>Brightline Retrofit Co. — Business Card</title>
<link rel="stylesheet" href="https://fonts.googleapis.com/css2?family=Roboto:wght@400;500;700&family=Roboto+Condensed:wght@500;700&display=swap">
<style>
  :root {
    --backdrop: #5a493b;
    --paper: #f2f2f2;
    --green-bright: #0a7e37;
    --green-deep: #12380f;
    --green-lime: #64be52;
    --green-logo: #1a6b2c;
    --white: #ffffff;
  }
  * { box-sizing: border-box; margin: 0; padding: 0; }
  html, body { width: 1200px; height: 960px; overflow: hidden; }
  body {
    background: var(--backdrop);
    font-family: "Roboto", Arial, sans-serif;
    position: relative;
  }
  .card {
    position: absolute;
    box-shadow: 2px 3px 4px rgba(0,0,0,0.35);
    overflow: hidden;
  }
  .card--front { left: 314px; top: 113px; width: 601px; height: 343px; }
  .card--back { left: 311px; top: 472px; width: 600px; height: 343px; background: var(--green-lime); }

  .front__brand {
    position: absolute; left: 0; top: 0; width: 323px; height: 343px;
    background: var(--paper);
    display: flex; align-items: center; justify-content: center; gap: 10px;
  }
  .brand-name {
    font-family: "Roboto", Arial, sans-serif;
    font-weight: 700;
    color: var(--green-logo);
    font-size: 26px;
    letter-spacing: 0.5px;
  }
  .brand-mark { width: 16px; height: 16px; background: var(--green-logo); }

  .front__details { position: absolute; left: 323px; top: 0; width: 278px; height: 343px; }
  .details__bg { position: absolute; inset: 0; }
  .person { position: absolute; left: 40px; top: 33px; color: var(--white); }
  .person__name { font-family: "Roboto Condensed", Arial, sans-serif; font-weight: 700; font-size: 23px; line-height: 1; }
  .person__title { font-family: "Roboto Condensed", Arial, sans-serif; font-weight: 500; font-size: 15px; margin-top: 6px; }

  .contact { position: absolute; right: 33px; top: 174px; color: var(--white); font-size: 14.5px; text-align: right; list-style: none; }
  .contact__address { line-height: 18px; margin-bottom: 7px; }
  .contact__item { display: flex; justify-content: flex-end; align-items: center; gap: 6px; height: 19px; }
  .contact__item svg { width: 14px; height: 14px; fill: var(--white); }

  .back__brand {
    position: absolute; left: 0; right: 0; top: 118px;
    display: flex; justify-content: center; align-items: center; gap: 16px;
  }
  .back__brand .brand-name { color: var(--white); font-size: 44px; }
  .back__brand .brand-mark { width: 26px; height: 26px; background: var(--white); }
  .back__web {
    position: absolute; left: 0; right: 0; top: 282px; text-align: center;
    color: var(--white); font-size: 14px; letter-spacing: 2.6px;
  }
</style>
</head>
<body>
  <section class="card card--front">
    <div class="front__brand">
      <span class="brand-name">Brightline Retrofit Co.</span>
      <span class="brand-mark"></span>
    </div>
    <div class="front__details">
      <svg class="details__bg" viewBox="0 0 278 343" width="278" height="343">
        <rect width="278" height="343" fill="var(--green-deep)"/>
        <polygon points="0,0 278,0 278,74 0,162" fill="var(--green-bright)"/>
        <line x1="0" y1="162" x2="278" y2="74" stroke="var(--white)" stroke-width="3"/>
      </svg>
      <div class="person">
        <div class="person__name">DANA MERCER</div>
        <div class="person__title">CEO/FOUNDER</div>
      </div>
      <ul class="contact">
        <li class="contact__address">2140 Alder Court<br>Fairbanks, Alaska 99701</li>
        <li class="contact__item">555 014 2291
          <svg viewBox="0 0 24 24"><path d="M6.6 10.8a15 15 0 0 0 6.6 6.6l2.2-2.2c.3-.3.7-.4 1-.2 1.1.4 2.3.6 3.6.6.6 0 1 .4 1 1V20c0 .6-.4 1-1 1A17 17 0 0 1 3 4c0-.6.4-1 1-1h3.5c.6 0 1 .4 1 1 0 1.3.2 2.5.6 3.6.1.3 0 .7-.2 1z"/></svg>
        </li>
        <li class="contact__item">555 017 8830
          <svg viewBox="0 0 24 24"><path d="M7 1h10a2 2 0 0 1 2 2v18a2 2 0 0 1-2 2H7a2 2 0 0 1-2-2V3a2 2 0 0 1 2-2zm0 3v14h10V4zm5 15.5a1 1 0 1 0 0 2 1 1 0 0 0 0-2z"/></svg>
        </li>
        <li class="contact__item">555 019 4472
          <svg viewBox="0 0 24 24"><path d="M6 2h12v5H6zM3 8h18a2 2 0 0 1 2 2v7h-4v5H5v-5H1v-7a2 2 0 0 1 2-2zm4 8v4h10v-4z"/></svg>
        </li>
        <li class="contact__item">dana@brightline.test
          <svg viewBox="0 0 24 24"><path d="M2 5h20v14H2zm2 2v.5l8 5 8-5V7l-8 5z"/></svg>
        </li>
        <li class="contact__item">www.brightline.test
          <svg viewBox="0 0 24 24"><path d="M12 2a10 10 0 1 0 0 20 10 10 0 0 0 0-20zm-1 17.9A8 8 0 0 1 4.1 10l4.9 5v1a2 2 0 0 0 2 2zm6.9-2.5A2 2 0 0 0 16 16h-1v-3a1 1 0 0 0-1-1H8v-2h2a1 1 0 0 0 1-1V7h2a2 2 0 0 0 2-2v-.4a8 8 0 0 1 2.9 12.8z"/></svg>
        </li>
      </ul>
    </div>
  </section>

  <section class="card card--back">
    <div class="back__brand">
      <span class="brand-name">Brightline Retrofit Co.</span>
      <span class="brand-mark"></span>
    </div>
    <div class="back__web">www.brightlineretrofit.test</div>
  </section>
</body>
</html>
```